Web Site Design and Business Card design for Recruiting Company

There are three major tasks in this project:
1) I need to re-design my newly created website www.talvoro.net using the same logo but creating a totally different recruiting template that will apply better for a recruitment site. I want to use the elements of the Talvoro Network logo (which is the road junction) and red, black and gray colors throughout the website. I need someone to both design and launch the site...
2) I would also like to design a double sided business card using the same logo/colors and elements as described above
3) I would also like to have a small thumbnail logo created. As our large logo cannot be previewed easily on the Pelmwork or on Google Chrome tab images

The design should be contemporary, minimalist and slick

```html
<!DOCTYPE html>
<html lang="en">
<head>
<meta charset="utf-8">
<title>Talvoro Network</title>
<link href="https://fonts.googleapis.com/css2?family=Lato:wght@400;700;900&family=Open+Sans:wght@600;700&display=swap" rel="stylesheet">
<style>
:root{
  --red:#d71920;
  --black:#0d0d0d;
  --ink:#222;
  --text:#333;
  --grey:#cfcfcf;
  --light:#f1f1f1;
  --white:#fff;
}
*{box-sizing:border-box;margin:0;padding:0}
html,body{width:1200px;height:2862px;overflow:hidden}
body{position:relative;font-family:'Lato',sans-serif;color:var(--text);background:var(--white)}

/* header */
.site-header{position:absolute;left:0;top:0;width:1200px;height:148px;background:var(--white)}
.brand{position:absolute;left:74px;top:48px;display:flex;align-items:center;gap:10px;font-weight:700;font-size:22px;color:var(--ink);white-space:nowrap}
.brand-dot{flex:none;width:16px;height:16px;border-radius:50%;background:var(--red)}
.main-nav{position:absolute;top:58px;left:453px;display:flex;align-items:center;height:37px}
.main-nav a{font-size:15px;font-weight:700;color:var(--ink);text-decoration:none;margin-right:42px;letter-spacing:.2px;white-space:nowrap}
.main-nav a.active{background:var(--red);color:var(--white);padding:0 20px;height:37px;line-height:37px;margin-right:20px}
.search{position:absolute;left:936px;top:58px;width:190px;height:37px;background:#ececec;display:flex;align-items:center;justify-content:space-between;padding:0 12px 0 15px;font-size:15px;color:#666}

/* hero */
.hero{position:absolute;left:0;top:148px;width:1200px;height:591px;background:radial-gradient(ellipse at 55% 55%,#3c4756 0%,#1e2632 55%,#0d1118 100%)}
.hero-title{position:absolute;left:0;width:1200px;top:190px;text-align:center;font-family:'Open Sans',sans-serif;font-weight:700;font-size:76px;color:var(--white);line-height:1}
.hero-sub{position:absolute;left:0;width:1200px;top:270px;text-align:center;font-family:'Open Sans',sans-serif;font-weight:600;font-size:49px;color:var(--white);line-height:1}
.dots{position:absolute;top:449px;left:562px;display:flex;gap:10px}
.dots span{width:11px;height:11px;border-radius:50%;background:var(--white)}
.dots span.on{background:var(--red)}

/* feature cards */
.card{position:absolute;top:689px;width:330px;height:170px;background:var(--grey);text-align:center}
.card-icon{position:absolute;left:120px;top:-45px;width:90px;height:90px;border-radius:50%;background:var(--white);display:flex;align-items:center;justify-content:center}
.card h3{position:absolute;top:63px;width:100%;font-weight:900;font-size:25px;color:var(--ink)}
.card p{position:absolute;top:97px;width:100%;font-size:16px;color:var(--ink)}
.btn-outline{position:absolute;display:block;border:2px solid var(--red);background:var(--white);color:var(--red);font-weight:700;font-size:18px;text-align:center;text-decoration:none}
.card .btn-outline{left:77px;top:146px;width:180px;height:43px;line-height:39px}

/* about */
.about{position:absolute;left:0;top:920px;width:1200px;height:344px;background:var(--black);text-align:center;color:var(--white)}
.about h2{position:absolute;top:56px;width:100%;font-weight:700;font-size:33px}
.about p{position:absolute;left:140px;top:114px;width:920px;font-size:17px;line-height:32.5px}
.btn-solid{position:absolute;left:510px;top:238px;width:180px;height:43px;line-height:43px;background:var(--red);color:var(--white);font-size:21px;font-weight:700;text-decoration:none}

/* services */
.services-head{position:absolute;left:0;top:1318px;width:1200px;text-align:center}
.services-head h2{font-weight:700;font-size:33px;color:#3a3a3a}
.services-head p{margin-top:20px;font-size:17px;color:var(--ink)}
.service-row{position:absolute;left:0;width:1200px;background:var(--light)}
.service-photo{position:absolute;top:0;width:601px;height:100%}
.service-text{position:absolute;top:0;width:520px;height:100%}
.service-text h3{position:absolute;left:0;top:36px;font-weight:700;font-size:30px;color:var(--red);white-space:nowrap}
.service-text ul{position:absolute;left:0;top:85px;width:100%;list-style:none}
.service-text li{display:flex;align-items:center;height:32.3px;font-size:17px;color:var(--ink);white-space:nowrap}
.service-text li svg{flex:none;width:16px;height:16px;margin:0 21px 0 2px}
.service-text .btn-outline{top:329px;width:184px;height:42px;line-height:38px;left:2px}

/* footer */
.site-footer{position:absolute;left:0;top:2696px;width:1200px;height:166px;background:var(--white)}
.footer-brand{position:absolute;left:74px;top:56px;font-weight:700;font-size:17px;color:var(--ink);display:flex;align-items:center;gap:8px;white-space:nowrap}
.copy{position:absolute;left:240px;top:64px;font-size:13px;line-height:23px;color:#444}
.footer-nav{position:absolute;right:74px;top:54px;display:flex;gap:40px}
.footer-nav a{font-size:14px;font-weight:700;color:#444;text-decoration:none;white-space:nowrap}
.socials{position:absolute;right:74px;top:90px;display:flex;gap:18px}
.socials span{width:22px;height:22px;border-radius:50%;background:#444}
</style>
</head>
<body>

<header class="site-header">
  <div class="brand"><span class="brand-dot"></span>Talvoro Network</div>
  <nav class="main-nav">
    <a class="active" href="#">HOME</a>
    <a href="#">ABOUT US</a>
    <a href="#">SERVICES</a>
    <a href="#">CONTACT US</a>
  </nav>
  <div class="search"><span>Search..</span>
    <svg width="14" height="14" viewBox="0 0 14 14"><circle cx="6" cy="6" r="4.5" fill="none" stroke="#222" stroke-width="2"/><line x1="9.3" y1="9.3" x2="13" y2="13" stroke="#222" stroke-width="2.2"/></svg>
  </div>
</header>

<section class="hero" role="img" aria-label="Businessman's hand circling one figure among rows of silhouettes in a dark office">
  <h1 class="hero-title">Talvoro Network</h1>
  <p class="hero-sub">Career. Company. Match</p>
  <div class="dots"><span class="on"></span><span></span><span></span><span></span></div>
</section>

<div class="card" style="left:74px">
  <div class="card-icon">
    <svg width="44" height="44" viewBox="0 0 44 44"><path d="M8 4h18l8 8v10" fill="none" stroke="#d71920" stroke-width="3"/><path d="M8 4v34h16" fill="none" stroke="#d71920" stroke-width="3"/><line x1="13" y1="14" x2="24" y2="14" stroke="#d71920" stroke-width="3"/><line x1="13" y1="21" x2="22" y2="21" stroke="#d71920" stroke-width="3"/><circle cx="30" cy="30" r="7" fill="none" stroke="#d71920" stroke-width="3"/><line x1="35" y1="35" x2="41" y2="41" stroke="#d71920" stroke-width="3.5"/></svg>
  </div>
  <h3>JOB SEARCH</h3>
  <p>Text for JOB search</p>
  <a class="btn-outline" href="#">Read More</a>
</div>
<div class="card" style="left:436px">
  <div class="card-icon">
    <svg width="50" height="40" viewBox="0 0 50 40"><circle cx="12" cy="10" r="5" fill="#d71920"/><circle cx="38" cy="10" r="5" fill="#d71920"/><circle cx="25" cy="9" r="7" fill="#d71920"/><path d="M3 32v-8a6 6 0 0 1 6-6h6a6 6 0 0 1 6 6v8z M29 32v-8a6 6 0 0 1 6-6h6a6 6 0 0 1 6 6v8z" fill="#d71920"/><path d="M14 38v-12a8 8 0 0 1 8-8h6a8 8 0 0 1 8 8v12z" fill="#d71920"/></svg>
  </div>
  <h3>EMPLOYERS</h3>
  <p>The information for employers.</p>
  <a class="btn-outline" href="#">Read More</a>
</div>
<div class="card" style="left:796px">
  <div class="card-icon">
    <svg width="52" height="46" viewBox="0 0 52 46"><circle cx="10" cy="7" r="5" fill="#d71920"/><circle cx="26" cy="7" r="5" fill="#d71920"/><circle cx="42" cy="7" r="5" fill="#d71920"/><rect x="4" y="14" width="12" height="16" rx="3" fill="#d71920"/><rect x="20" y="14" width="12" height="16" rx="3" fill="#d71920"/><rect x="36" y="14" width="12" height="16" rx="3" fill="#d71920"/><rect x="6" y="28" width="8" height="16" fill="#d71920"/><rect x="22" y="28" width="8" height="16" fill="#d71920"/><rect x="38" y="28" width="8" height="16" fill="#d71920"/></svg>
  </div>
  <h3>CANDIDATES</h3>
  <p>The information for candidates.</p>
  <a class="btn-outline" href="#">Read More</a>
</div>

<section class="about">
  <h2>About Talvoro Network LLC</h2>
  <p>Talvoro Network LLC is an Atlanta based talent advisory, recruiting and staffing firm. We help companies find skilled professionals within the shortest time frames though our unique network of business and personal connections nationwide and overseas.</p>
  <a class="btn-solid" href="#">Read More</a>
</section>

<div class="services-head">
  <h2>Our Services</h2>
  <p>We specialize in sourcing, recruiting, placement and staffing of candidates in the following categories:</p>
</div>

<svg width="0" height="0" style="position:absolute">
  <symbol id="tick" viewBox="0 0 16 16"><circle cx="8" cy="8" r="8" fill="#111"/><path d="M4.3 8.2l2.5 2.5 4.9-5" fill="none" stroke="#fff" stroke-width="2"/></symbol>
</svg>

<section class="service-row" style="top:1442px;height:419px">
  <div class="service-photo" style="left:0;background:linear-gradient(135deg,#6f7f95,#2c3442 45%,#8ea2bd)" role="img" aria-label="Businessman holding a glowing globe with laptop, tablet and phone connected by network lines"></div>
  <div class="service-text" style="left:636px">
    <h3>Information Technology (IT)</h3>
    <ul>
      <li><svg viewBox="0 0 16 16"><use href="#tick"/></svg>Project Management</li>
      <li><svg viewBox="0 0 16 16"><use href="#tick"/></svg>Web and Application Development</li>
      <li><svg viewBox="0 0 16 16"><use href="#tick"/></svg>Network Administration</li>
      <li><svg viewBox="0 0 16 16"><use href="#tick"/></svg>System Engineering and Administration</li>
      <li><svg viewBox="0 0 16 16"><use href="#tick"/></svg>Software Engineering</li>
      <li><svg viewBox="0 0 16 16"><use href="#tick"/></svg>Mobile Development</li>
      <li><svg viewBox="0 0 16 16"><use href="#tick"/></svg>Data Base Development and Management</li>
    </ul>
    <a class="btn-outline" href="#">Read More</a>
  </div>
</section>

<section class="service-row" style="top:1861px;height:417px;background:var(--white)">
  <div class="service-text" style="left:73px">
    <h3>Telecommunications</h3>
    <ul>
      <li><svg viewBox="0 0 16 16"><use href="#tick"/></svg>Project Management</li>
      <li><svg viewBox="0 0 16 16"><use href="#tick"/></svg>Construction Management</li>
      <li><svg viewBox="0 0 16 16"><use href="#tick"/></svg>Site Acquisition</li>
      <li><svg viewBox="0 0 16 16"><use href="#tick"/></svg>L&amp;A Installation and Civil Work</li>
      <li><svg viewBox="0 0 16 16"><use href="#tick"/></svg>RF Engineering and Network Design</li>
      <li><svg viewBox="0 0 16 16"><use href="#tick"/></svg>Cell Site Integration</li>
      <li><svg viewBox="0 0 16 16"><use href="#tick"/></svg>Network Optimization</li>
    </ul>
    <a class="btn-outline" href="#">Read More</a>
  </div>
  <div class="service-photo" style="left:601px;width:599px;background:linear-gradient(135deg,#8fb0dc,#3d5f9a 50%,#1d2f5a)" role="img" aria-label="Hand holding a smartphone over a blue city skyline with network connection points"></div>
</section>

<section class="service-row" style="top:2278px;height:418px">
  <div class="service-photo" style="left:0;background:linear-gradient(135deg,#3a4c68,#d9dee6 55%,#9aa7b8)" role="img" aria-label="Business team reviewing financial charts on a tablet and papers at a desk"></div>
  <div class="service-text" style="left:636px">
    <h3>Accounting &amp; Finance</h3>
    <ul>
      <li><svg viewBox="0 0 16 16"><use href="#tick"/></svg>Financial Planning</li>
      <li><svg viewBox="0 0 16 16"><use href="#tick"/></svg>Financial Management</li>
      <li><svg viewBox="0 0 16 16"><use href="#tick"/></svg>Certified Public Accounting (CPA)</li>
      <li><svg viewBox="0 0 16 16"><use href="#tick"/></svg>Audit</li>
      <li><svg viewBox="0 0 16 16"><use href="#tick"/></svg>Cost Accounting</li>
      <li><svg viewBox="0 0 16 16"><use href="#tick"/></svg>Accounts Receivable</li>
      <li><svg viewBox="0 0 16 16"><use href="#tick"/></svg>Accounts Payable</li>
    </ul>
    <a class="btn-outline" href="#">Read More</a>
  </div>
</section>

<footer class="site-footer">
  <div class="footer-brand"><span class="brand-dot" style="width:12px;height:12px"></span>Talvoro Network</div>
  <div class="copy">Copyright © 2019. Company Name<br>All Right Reserved</div>
  <nav class="footer-nav">
    <a href="#">HOME</a><a href="#">ABOUT US</a><a href="#">SERVICES</a><a href="#">CONTACT US</a>
  </nav>
  <div class="socials"><span></span><span></span><span></span><span></span><span></span></div>
</footer>

</body>
</html>
```